Marlow Veston Orthodontics Ecommerce

We need to design an ecommerce website for a medical device company that specializes in orthodontics. With being a medical company, we will need to have two experiences for when a user visits our site. One for a non-registered user that will not show an pricing for the products and the other for a registered user that will show the price of the product. Ideally we would like a clean, modern design that utilizes our colors and is also is mobile friendly.

The current website: marlowvestonortho.com may be used a guide for the type of content and colors we used, but does not need to adhere to it.

Main colors to keep are the ones in the logo. Red, Blue and White.

Target Market(s)

Orthodontists, Dental

Industry/Entity Type

It Company

Coding

Coded - Design and coding required

Font styles to use
Sans Serif

Colors

Designer to choose colors to be used in the design.

Requirements
Must have
• Homepage, Product Family page, Product page and Contact Us Page. The design should work with any PC or mobile device to keep the user experience consistent.
Nice to have
• The quibrel.com website has a great feel to it and it would be nice to have something similar. Also, video is starting to become a big part of what we use to advertise and educate users about our products. It would be nice if we can incorporate video we possible to give users the ability to view them.
Should not have
• The design should be easy for users to navigate and use to locate the product they are interested in. It should not be confusing or too cluttered were a user can get lost.

```html
<!DOCTYPE html>
<html lang="en">
<head>
<meta charset="utf-8">
<title>Marlow Veston Orthodontics</title>
<link rel="stylesheet" href="https://fonts.googleapis.com/css2?family=Open+Sans:wght@400;600;700&family=Raleway:wght@300;400;600;700&display=swap">
<style>
:root{
  --ink:#2b2b2b;
  --muted:#6b6b6b;
  --header:#2d2d2f;
  --footer:#1c1c1e;
  --footer-2:#2a2a2c;
  --red:#c8202f;
  --blue:#1f7fc4;
  --blue-dark:#17629a;
  --paper:#ffffff;
  --mist:#f1f2f4;
  --hero-a:#eceff2;
  --glove:#5fa3d6;
  --steel-a:#e4e6e9;
  --steel-b:#8e949b;
  --ice-a:#e8f3fc;
  --ice-b:#a9cdec;
  --blush-a:#fcebed;
  --blush-b:#efb7c0;
}
*{box-sizing:border-box;margin:0;padding:0}
html,body{width:1200px;height:2824px;overflow:hidden;background:var(--paper)}
body{font-family:"Open Sans",sans-serif;color:var(--ink)}
.page{width:1200px;height:2824px;display:flex;flex-direction:column}

.site-header{height:64px;flex:none;background:var(--header);display:flex;align-items:center;padding:0 48px;gap:40px;border-bottom:3px solid var(--red)}
.brand{display:flex;align-items:center;gap:10px;color:#fff;font-family:"Raleway",sans-serif;font-weight:600;font-size:15px}
.brand-mark{width:14px;height:14px;background:var(--red)}
.main-nav{display:flex;gap:34px;margin-left:auto;list-style:none}
.main-nav li{color:#e6e6e6;font-size:12px;font-weight:600;letter-spacing:.5px}
.header-tools{display:flex;gap:14px}
.header-tools span{width:16px;height:16px;border:2px solid #d0d0d0;border-radius:50%}

.hero{height:600px;flex:none;position:relative;background:var(--hero-a);overflow:hidden}
.hero-photo{position:absolute;right:0;top:0;width:64%;height:100%;
  background:
    radial-gradient(ellipse 38% 30% at 48% 62%,#fbfbf9 0%,rgba(251,251,249,.85) 40%,rgba(251,251,249,0) 100%),
    radial-gradient(ellipse 40% 45% at 88% 18%,var(--glove) 0%,rgba(95,163,214,.6) 45%,rgba(95,163,214,0) 100%),
    radial-gradient(ellipse 45% 40% at 78% 95%,#4d93c9 0%,rgba(77,147,201,.5) 50%,rgba(77,147,201,0) 100%),
    linear-gradient(100deg,var(--hero-a) 0%,#dfe5ea 40%,#c3ced7 100%)}
.hero-copy{position:absolute;left:64px;top:170px;width:640px}
.hero-title{font-family:"Raleway",sans-serif;font-variant:small-caps;font-weight:700;font-size:36px;line-height:1.25;color:var(--ink)}
.hero-sub{margin-top:16px;font-size:13px;color:var(--muted)}
.btn-dark{display:inline-block;margin-top:26px;background:var(--header);color:#fff;font-size:12px;font-weight:600;padding:11px 22px}

.intraoral{height:520px;flex:none;padding:56px 64px 0}
.section-title{font-family:"Raleway",sans-serif;font-variant:small-caps;font-weight:700;font-size:26px;color:var(--ink)}
.section-rule{width:100%;height:1px;background:#e2e2e2;margin:14px 0 48px}
.carousel{display:flex;align-items:center;gap:22px}
.carousel-arrow{width:30px;height:30px;border-radius:50%;background:var(--blue);flex:none;display:flex;align-items:center;justify-content:center}
.carousel-arrow.ghost{background:#e4e6e8}
.product-cards{display:flex;gap:26px;flex:1}
.product-card{flex:1;border:1px solid #e5e5e5}
.product-shot{height:230px;background:radial-gradient(ellipse 45% 22% at 50% 55%,#c9cdd2 0%,rgba(201,205,210,.4) 55%,rgba(255,255,255,0) 100%),linear-gradient(180deg,#fafafa,#eceef0)}
.product-card:nth-child(2) .product-shot{background:radial-gradient(ellipse 22% 30% at 50% 52%,#b9bec4 0%,rgba(185,190,196,.45) 55%,rgba(255,255,255,0) 100%),linear-gradient(180deg,#fafafa,#eceef0)}
.product-card:nth-child(3) .product-shot{background:radial-gradient(ellipse 40% 26% at 50% 52%,#a9b7e0 0%,#d9b4cd 45%,rgba(255,255,255,0) 100%),linear-gradient(180deg,#fafafa,#eceef0)}
.product-name{background:var(--blue);color:#fff;font-size:13px;padding:12px 16px}
.product-card:not(:first-child) .product-name{background:#5e9fd0}

.feature{height:440px;flex:none;display:flex}
.feature-text{width:50%;padding:70px 64px;background:var(--mist)}
.feature-text.white{background:var(--paper)}
.feature-title{font-family:"Raleway",sans-serif;font-weight:300;font-size:30px;color:#4a4a4a}
.feature-sub{margin-top:14px;font-size:13px;font-weight:700}
.feature-body{margin-top:12px;font-size:11.5px;line-height:1.7;color:var(--muted);max-width:470px}
.feature-link{margin-top:14px;font-size:11px;font-weight:700}
.btn-outline{display:inline-block;margin-top:16px;border:1px solid #9a9a9a;font-size:10.5px;padding:6px 14px;color:var(--ink)}
.feature-shot{width:50%}
.shot-steel{background:radial-gradient(ellipse 34% 38% at 50% 50%,#f7f8f9 0%,#c4c8cd 50%,rgba(196,200,205,0) 100%),radial-gradient(circle at 50% 50%,var(--steel-a) 0%,var(--steel-b) 100%)}
.shot-ice{background:radial-gradient(ellipse 34% 38% at 50% 50%,#ffffff 0%,#d6e9f8 55%,rgba(214,233,248,0) 100%),radial-gradient(circle at 50% 50%,var(--ice-a) 0%,var(--ice-b) 100%)}
.shot-blush{background:radial-gradient(ellipse 30% 34% at 50% 50%,#dadcdf 0%,#b8bcc1 45%,rgba(184,188,193,0) 100%),radial-gradient(circle at 50% 50%,var(--blush-a) 0%,var(--blush-b) 100%)}

.site-footer{flex:1;display:flex;flex-direction:column;background:linear-gradient(160deg,var(--footer-2) 0%,var(--footer) 60%);border-top:4px solid var(--red);padding:40px 64px 28px;color:#cfcfcf}
.footer-cols{display:flex;gap:60px}
.footer-col{flex:1}
.footer-col h4{font-size:12px;font-weight:700;color:#fff;letter-spacing:1px;padding-bottom:10px;border-bottom:1px solid #444;margin-bottom:10px}
.footer-col ul{list-style:none}
.footer-col li{font-size:11.5px;line-height:1.9;color:#b9b9b9}
.footer-bottom{margin-top:auto;display:flex;align-items:center;justify-content:space-between;border-top:1px solid #3a3a3a;padding-top:20px}
.footer-brand{display:flex;align-items:center;gap:10px;color:#fff;font-family:"Raleway",sans-serif;font-weight:600;font-size:15px}
.copyright{font-size:11px;color:#8d8d8d;margin-top:6px}
.social{display:flex;gap:12px}
.social span{width:34px;height:34px;border-radius:50%;background:#4a4a4d}
</style>
</head>
<body>
<div class="page">
  <header class="site-header">
    <div class="brand"><span class="brand-mark"></span>Marlow Veston Orthodontics</div>
    <ul class="main-nav">
      <li>Products</li><li>Practice Solutions</li><li>Education</li><li>About Us</li><li>Contact Us</li>
    </ul>
    <div class="header-tools"><span></span><span></span></div>
  </header>

  <section class="hero">
    <div class="hero-photo" role="img" aria-label="Gloved hand holding an orthodontic instrument over a dental model with braces"></div>
    <div class="hero-copy">
      <h1 class="hero-title">Orthodontic Excellence &amp; Technology<br>Value, Quality, Innovation</h1>
      <p class="hero-sub">Trusted products for modern orthodontic practices</p>
      <span class="btn-dark">View All Items</span>
    </div>
  </section>

  <section class="intraoral">
    <h2 class="section-title">Intraoral Products</h2>
    <div class="section-rule"></div>
    <div class="carousel">
      <span class="carousel-arrow">
        <svg width="10" height="10" viewBox="0 0 10 10"><path d="M7 1 3 5l4 4" fill="none" stroke="#fff" stroke-width="2"/></svg>
      </span>
      <div class="product-cards">
        <div class="product-card"><div class="product-shot" role="img" aria-label="Ratchet positioning instrument"></div><div class="product-name">Ratchet Positioning</div></div>
        <div class="product-card"><div class="product-shot" role="img" aria-label="Corvell arch attachment"></div><div class="product-name">Corvell Attachm...</div></div>
        <div class="product-card"><div class="product-shot" role="img" aria-label="Coloured archwire"></div><div class="product-name">Corvell Archwire 3D</div></div>
      </div>
      <span class="carousel-arrow ghost">
        <svg width="10" height="10" viewBox="0 0 10 10"><path d="M3 1l4 4-4 4" fill="none" stroke="#888" stroke-width="2"/></svg>
      </span>
    </div>
  </section>

  <section class="feature">
    <div class="feature-text">
      <h3 class="feature-title">Brackets</h3>
      <p class="feature-sub">KLV™ Self Ligating Bracket</p>
      <p class="feature-body">A low profile self ligating bracket designed for efficient treatment and patient comfort. Smooth contours and a secure clip make archwire changes fast, while precise slot tolerances deliver reliable control from start to finish.</p>
      <p class="feature-link">Read More »</p>
      <span class="btn-outline">Buy Now</span>
    </div>
    <div class="feature-shot shot-steel" role="img" aria-label="Metal self ligating bracket close-up"></div>
  </section>

  <section class="feature">
    <div class="feature-shot shot-ice" role="img" aria-label="Clear ceramic bracket close-up"></div>
    <div class="feature-text white">
      <h3 class="feature-title">Ceramic Bracket System</h3>
      <p class="feature-sub">ClearVane Plus™ Sapphire Ceramic Bracket System</p>
      <p class="feature-body">Aesthetic sapphire brackets that blend with natural enamel. Strong, stain resistant and easy to debond, they give patients a discreet option without giving up clinical performance or bond strength.</p>
      <p class="feature-link">Read More »</p>
      <span class="btn-outline">Buy Now</span>
    </div>
  </section>

  <section class="feature">
    <div class="feature-text">
      <h3 class="feature-title">Halvern-2™ Appliance</h3>
      <p class="feature-sub">Halvern-2™ Appliance</p>
      <p class="feature-body">A straight wire appliance built around precise prescription values. Each bracket carries its own torque and angulation, reducing wire bending and helping practices reach consistent finishing results.</p>
      <p class="feature-link">Read More »</p>
      <span class="btn-outline">Buy Now</span>
    </div>
    <div class="feature-shot shot-blush" role="img" aria-label="Metal appliance bracket close-up"></div>
  </section>

  <footer class="site-footer">
    <div class="footer-cols">
      <div class="footer-col">
        <h4>CONTACT US</h4>
        <ul><li>Customer Service</li><li>Phone: 800-555-0142</li><li>Fax: 800-555-0187</li><li>Mon–Fri 8am–5pm</li><li>marlowvestonortho.com</li></ul>
      </div>
      <div class="footer-col">
        <h4>PRODUCTS</h4>
        <ul><li>Brackets</li><li>Archwires</li><li>Bands &amp; Tubes</li><li>Elastomerics</li><li>Instruments</li><li>Appliances</li></ul>
      </div>
      <div class="footer-col">
        <h4>PRACTICE SOLUTIONS</h4>
        <ul><li>Practice Analysis</li><li>Digital Workflow</li><li>Financing Options</li><li>Continuing Education</li><li>Events</li></ul>
      </div>
      <div class="footer-col">
        <h4>ABOUT US</h4>
        <ul><li>Our Story</li><li>Careers</li><li>News</li><li>Privacy Policy</li><li>Terms of Use</li></ul>
      </div>
    </div>
    <div class="footer-bottom">
      <div>
        <div class="footer-brand"><span class="brand-mark"></span>Marlow Veston Orthodontics</div>
        <p class="copyright">© Marlow Veston Orthodontics. All rights reserved.</p>
      </div>
      <div class="social"><span></span><span></span><span></span><span></span></div>
    </div>
  </footer>
</div>
</body>
</html>
```